R7M Horizon Business Card Design

We need a business card created for our New Business "R7M Horizon"<br/><br/>The business card design is up to you however the following information must be on the business card:<br/><br/>Front of the business card -<br/>Email :darrenp@r7mhorizon.nz<br/>Mobile: +64 (0) 22 4870 619<br/>Website: www.r7mhorizon.nz<br/>Card Owner Name: Darren Paltrow<br/>Company Title: Business Development Manager<br/>Slogan: "The BEST of both worlds". <br/>Logo On the front attached to the design brief<br/><br/>On the back: <br/>Space on the back for 4 more versions of the logo across the bottom of the card indicating different subsidiary brands - R7M Coffee, R7M Arts, R7M ?? (The card will be used for all of these brands - We Will add the extra subsidiary logos to the design once the design is finished (We are a graphics design team). <br/><br/>Other than that we want a premium feeling logo that remains universally usable depending on the business entity that we are using the card for. The use of bright bold colours would be great but we still want the card to feel premium.
Target Market(s)
Gift Design and Manufacturing Companies
Contact Information for Business Card
Front of the business card -
Email :darrenp@r7mhorizon.nz
Mobile: +64 (0) 22 4870 619
Website: www.r7mhorizon.nz
Card Owner Name: Darren Paltrow
Company Title: Business Development Manager
Slogan: "The BEST of both worlds".
Logo On the front attached to the design brief

```html
<!DOCTYPE html>
<html lang="en">
<head>
<meta charset="UTF-8">
<title>R7M Horizon Business Card</title>
<link href="https://fonts.googleapis.com/css2?family=Exo+2:ital,wght@0,400;0,600;0,700;1,700&display=swap" rel="stylesheet">
<style>
  :root {
    --page: #161617;
    --card: #202123;
    --card-edge: #2a2b2e;
    --blue: #3a4cb0;
    --blue-faint: #262a44;
    --mark-dark: #2b2c30;
    --white: #ffffff;
    --text: #f1f1f3;
  }
  * { margin: 0; padding: 0; box-sizing: border-box; }
  html, body {
    width: 1200px; height: 900px; overflow: hidden;
    background: var(--page);
    font-family: "Exo 2", sans-serif;
  }
  .stage {
    position: relative; width: 1200px; height: 900px;
  }
  .card {
    position: absolute; left: 250px; width: 700px; height: 400px;
    background: var(--card);
    border: 1px solid var(--card-edge);
    overflow: hidden;
  }
  .card-back { top: 40px; }
  .card-front { top: 465px; }

  /* Back */
  .back-ring {
    position: absolute; left: 200px; top: 50px;
    width: 300px; height: 300px; border-radius: 50%;
    border: 6px solid var(--blue-faint);
  }
  .back-name {
    position: absolute; left: 0; right: 0; top: 172px;
    text-align: center;
    font-weight: 700; font-size: 46px; letter-spacing: 1px;
    color: var(--mark-dark);
  }

  /* Front */
  .brand-name {
    position: absolute; left: 48px; top: 40px;
    font-weight: 700; font-size: 46px; letter-spacing: 1px;
    color: var(--blue);
  }
  .holder-name {
    position: absolute; left: 48px; top: 130px;
    font-weight: 700; font-style: italic; font-size: 28px;
    text-transform: uppercase; color: var(--blue); letter-spacing: 0.5px;
  }
  .holder-title {
    position: absolute; left: 48px; top: 166px;
    font-weight: 400; font-size: 20px; color: var(--text);
  }
  .divider {
    position: absolute; left: 40px; right: 60px; top: 212px;
    height: 2px; background: var(--blue);
  }
  .contacts {
    position: absolute; left: 48px; top: 234px;
    list-style: none;
  }
  .contacts li {
    display: flex; align-items: center; gap: 12px;
    font-size: 19px; color: var(--text); line-height: 29px;
  }
  .contacts svg { width: 20px; height: 20px; flex: none; }
  .slogan {
    position: absolute; right: 60px; top: 298px;
    font-size: 22px; color: var(--blue);
  }
  .footer-stripes {
    position: absolute; left: 0; bottom: 0; width: 700px; height: 40px;
  }
</style>
</head>
<body>
<main class="stage">

  <section class="card card-back" aria-label="Card back">
    <div class="back-ring"></div>
    <div class="back-name">R7M Horizon</div>
  </section>

  <section class="card card-front" aria-label="Card front">
    <div class="brand-name">R7M Horizon</div>
    <h1 class="holder-name">Darren Paltrow</h1>
    <p class="holder-title">Business Development Manager</p>
    <div class="divider"></div>
    <ul class="contacts">
      <li>
        <svg viewBox="0 0 24 24" fill="none" stroke="#3a4cb0" stroke-width="1.8" stroke-linecap="round" stroke-linejoin="round">
          <circle cx="12" cy="12" r="10"/>
          <path d="M8.5 7.5c.5-.5 1.2-.4 1.5.1l1 1.6c.3.4.2 1-.2 1.3l-.6.5c.6 1.3 1.5 2.2 2.8 2.8l.5-.6c.3-.4.9-.5 1.3-.2l1.6 1c.5.3.6 1 .1 1.5-.9 1-2.3 1.2-3.5.5-2.2-1.2-3.8-2.8-5-5-.7-1.2-.5-2.6.5-3.5z"/>
        </svg>
        +64 (0) 22 4870 619
      </li>
      <li>
        <svg viewBox="0 0 24 24" fill="none" stroke="#3a4cb0" stroke-width="1.8" stroke-linejoin="round">
          <rect x="2.5" y="5.5" width="19" height="13" rx="1"/>
          <path d="M2.5 6l9.5 7 9.5-7"/>
        </svg>
        darrenp@r7mhorizon.nz
      </li>
      <li>
        <svg viewBox="0 0 24 24" fill="none" stroke="#3a4cb0" stroke-width="1.8">
          <circle cx="12" cy="12" r="9.5"/>
          <ellipse cx="12" cy="12" rx="4" ry="9.5"/>
          <path d="M2.5 12h19M4 7h16M4 17h16"/>
        </svg>
        www.r7mhorizon.nz
      </li>
    </ul>
    <p class="slogan">The BEST of both worlds</p>
    <svg class="footer-stripes" viewBox="0 0 700 40" aria-hidden="true">
      <polygon points="0,4 262,14 282,40 0,40" fill="#3a4cb0"/>
      <polygon points="292,26 700,30 700,40 302,40" fill="#ffffff"/>
    </svg>
  </section>

</main>
</body>
</html>
```